Design the main page for a travel security app

We are are doing web/app developments. The app will offer information about user travels, where they can find everything they need information about their reserved travels (like departure and destination airport, departure datetime, arrival datetime, flight number, destination risk), destination risks, travel advices (like general info, emergency telephone number,...), whether (and much more in the future).
The menu voices will be:
- Travels
- Travel Alerts
- Travel Advice
- Country Risk
- Travel Tips
- Options
The main colors will be red and black.
It should be able to look as good if it's small / enlarged.
The company's name is "Lanternfold".

```html
<!DOCTYPE html>
<html lang="en">
<head>
<meta charset="utf-8">
<title>Lanternfold – Travel Security</title>
<link href="https://fonts.googleapis.com/css2?family=Roboto:wght@300;400;700&display=swap" rel="stylesheet">
<style>
  :root {
    --red: #f20d0d;
    --red-dark: #e00000;
    --black: #111111;
    --ink: #2b2b2b;
    --white: #ffffff;
    --map-light: #f4f4f4;
    --map-mid: #c9c9c9;
  }
  * { margin: 0; padding: 0; box-sizing: border-box; }
  html, body { width: 711px; height: 1200px; overflow: hidden; background: var(--white); }
  body { font-family: "Roboto", Arial, sans-serif; color: var(--ink); }

  .screen { position: relative; width: 711px; height: 1200px; background: var(--white); overflow: hidden; }

  .status-bar {
    position: absolute; top: 0; left: 0; right: 0; height: 42px;
    background: var(--black); color: var(--white);
    display: flex; align-items: center; justify-content: flex-end; gap: 14px;
    padding-right: 18px; font-size: 30px; font-weight: 400;
  }
  .status-bar svg { display: block; }

  .app-header {
    position: absolute; top: 42px; left: 0; right: 0; height: 72px;
    background: var(--red);
    display: flex; align-items: center; justify-content: space-between;
    padding: 0 26px 0 28px;
  }
  .brand-name { font-size: 34px; font-weight: 700; color: var(--black); letter-spacing: 0.2px; }
  .header-actions { display: flex; align-items: center; gap: 18px; }

  .hero-visual {
    position: absolute; top: 120px; left: 0; width: 711px; height: 375px;
    background: radial-gradient(ellipse at 50% 45%, var(--map-mid) 0%, #dcdcdc 45%, var(--map-light) 75%, var(--white) 100%);
  }

  .hotline {
    position: absolute; top: 535px; left: 0; right: 0;
    display: flex; align-items: center; justify-content: center; gap: 14px;
    font-size: 58px; font-weight: 300; color: var(--ink);
  }

  .menu-item { position: absolute; width: 240px; height: 200px; margin-left: -120px; text-align: center; }
  .menu-icon {
    position: absolute; left: 50%; top: 0; width: 132px; height: 132px; margin-left: -66px;
    border: 4px solid var(--red); border-radius: 50%; background: var(--white);
    display: flex; align-items: center; justify-content: center;
  }
  .menu-label {
    position: absolute; top: 150px; left: 0; right: 0;
    font-size: 25px; font-weight: 400; color: var(--black);
  }
  .menu-rule { position: absolute; top: 178px; left: 14px; }

  .row-1 { top: 655px; }
  .row-2 { top: 925px; }
  .col-1 { left: 128px; }
  .col-2 { left: 355px; }
  .col-3 { left: 580px; }
</style>
</head>
<body>
<div class="screen">

  <div class="status-bar">
    <svg width="46" height="30" viewBox="0 0 46 30" aria-hidden="true">
      <rect x="2" y="22" width="6" height="8" fill="#777"/>
      <rect x="12" y="16" width="6" height="14" fill="#777"/>
      <rect x="22" y="9" width="6" height="21" fill="#777"/>
      <rect x="32" y="2" width="6" height="28" fill="#777"/>
    </svg>
    <svg width="20" height="34" viewBox="0 0 20 34" aria-hidden="true">
      <rect x="6" y="0" width="8" height="4" fill="#8fd14f"/>
      <rect x="1" y="4" width="18" height="30" rx="2" fill="#8fd14f"/>
      <path d="M11 8 L5 20 H10 L8 30 L15 16 H10 Z" fill="#111"/>
    </svg>
    <span class="clock-time">9:40 PM</span>
  </div>

  <header class="app-header">
    <span class="brand-name">Lanternfold</span>
    <div class="header-actions">
      <svg class="icon-bell" width="42" height="46" viewBox="0 0 42 46" aria-label="Notifications">
        <path d="M21 3 C12 3 8 10 8 18 V29 L3 36 H39 L34 29 V18 C34 10 30 3 21 3 Z" fill="var(--black)"/>
        <circle cx="21" cy="41" r="5" fill="var(--black)"/>
      </svg>
      <svg class="icon-menu" width="54" height="44" viewBox="0 0 54 44" aria-label="Menu">
        <rect x="0" y="2" width="54" height="9" fill="var(--black)"/>
        <rect x="0" y="17" width="54" height="9" fill="var(--black)"/>
        <rect x="0" y="32" width="54" height="9" fill="var(--black)"/>
      </svg>
    </div>
  </header>

  <div class="hero-visual" role="img" aria-label="Dotted world map with a large station clock and a paper plane flying across"></div>

  <div class="hotline">
    <svg width="56" height="44" viewBox="0 0 56 44" aria-hidden="true">
      <path d="M4 14 C4 4 52 4 52 14 V20 H40 V13 H16 V20 H4 Z" fill="var(--red)"/>
      <path d="M14 20 H42 L50 42 H6 Z" fill="var(--red)"/>
      <circle cx="28" cy="31" r="6" fill="var(--white)"/>
    </svg>
    <span class="hotline-number">0172-5550136</span>
  </div>

  <!-- Row 1 -->
  <div class="menu-item row-1 col-1">
    <div class="menu-icon">
      <svg width="80" height="80" viewBox="0 0 100 100" aria-hidden="true">
        <path d="M84 12 C90 8 94 12 90 18 L68 42 L80 82 L72 88 L54 54 L36 72 L38 86 L32 90 L24 74 L8 66 L12 60 L26 62 L44 44 L10 28 L16 20 L58 30 Z" fill="var(--red)"/>
      </svg>
    </div>
    <div class="menu-label">Travels</div>
    <svg class="menu-rule" width="212" height="16" viewBox="0 0 212 16" aria-hidden="true">
      <rect x="0" y="10" width="212" height="4" fill="var(--black)"/>
      <path d="M190 14 L198 0 L212 14 Z" fill="var(--black)"/>
    </svg>
  </div>

  <div class="menu-item row-1 col-2">
    <div class="menu-icon">
      <svg width="88" height="80" viewBox="0 0 100 90" aria-hidden="true">
        <path d="M50 4 L96 84 H4 Z" fill="var(--red)" stroke="var(--red)" stroke-width="6" stroke-linejoin="round"/>
        <rect x="45" y="30" width="10" height="32" fill="var(--white)"/>
        <rect x="45" y="68" width="10" height="10" fill="var(--white)"/>
      </svg>
    </div>
    <div class="menu-label">Travel Alerts</div>
    <svg class="menu-rule" width="212" height="16" viewBox="0 0 212 16" aria-hidden="true">
      <rect x="0" y="10" width="212" height="4" fill="var(--black)"/>
      <path d="M190 14 L198 0 L212 14 Z" fill="var(--black)"/>
    </svg>
  </div>

  <div class="menu-item row-1 col-3">
    <div class="menu-icon">
      <svg width="80" height="80" viewBox="0 0 100 100" aria-hidden="true">
        <path d="M30 10 H86 L72 74 H16 Z" fill="var(--red)"/>
        <path d="M16 74 H72 L70 84 H20 C12 84 12 74 16 74 Z" fill="none" stroke="var(--red)" stroke-width="6"/>
        <path d="M40 26 H72" stroke="var(--white)" stroke-width="4"/>
      </svg>
    </div>
    <div class="menu-label">Travel Advice</div>
    <svg class="menu-rule" width="212" height="16" viewBox="0 0 212 16" aria-hidden="true">
      <rect x="0" y="10" width="212" height="4" fill="var(--black)"/>
      <path d="M190 14 L198 0 L212 14 Z" fill="var(--black)"/>
    </svg>
  </div>

  <!-- Row 2 -->
  <div class="menu-item row-2 col-1">
    <div class="menu-icon">
      <svg width="86" height="86" viewBox="0 0 100 100" aria-hidden="true">
        <path d="M30 8 C15 8 8 20 8 30 C8 46 30 74 30 74 C30 74 52 46 52 30 C52 20 45 8 30 8 Z" fill="var(--red)"/>
        <circle cx="30" cy="30" r="9" fill="var(--white)"/>
        <path d="M72 20 C64 20 60 26 60 32 C60 42 72 58 72 58 C72 58 84 42 84 32 C84 26 80 20 72 20 Z" fill="var(--red)"/>
        <circle cx="72" cy="32" r="5" fill="var(--white)"/>
        <path d="M30 76 L72 60" stroke="var(--red)" stroke-width="2" stroke-dasharray="3 3"/>
      </svg>
    </div>
    <div class="menu-label">Country Risk</div>
    <svg class="menu-rule" width="212" height="16" viewBox="0 0 212 16" aria-hidden="true">
      <rect x="0" y="10" width="212" height="4" fill="var(--black)"/>
      <path d="M190 14 L198 0 L212 14 Z" fill="var(--black)"/>
    </svg>
  </div>

  <div class="menu-item row-2 col-2">
    <div class="menu-icon">
      <svg width="88" height="88" viewBox="0 0 100 100" aria-hidden="true">
        <path d="M6 46 C8 22 28 8 50 8 C72 8 92 22 94 46 C88 40 80 40 74 46 C68 40 58 40 50 46 C42 40 32 40 26 46 C20 40 12 40 6 46 Z" fill="var(--red)"/>
        <path d="M50 44 V84 C50 92 38 92 38 84" fill="none" stroke="var(--red)" stroke-width="5" stroke-linecap="round"/>
      </svg>
    </div>
    <div class="menu-label">Travel Tips</div>
    <svg class="menu-rule" width="212" height="16" viewBox="0 0 212 16" aria-hidden="true">
      <rect x="0" y="10" width="212" height="4" fill="var(--black)"/>
      <path d="M190 14 L198 0 L212 14 Z" fill="var(--black)"/>
    </svg>
  </div>

  <div class="menu-item row-2 col-3">
    <div class="menu-icon">
      <svg width="90" height="80" viewBox="0 0 100 90" aria-hidden="true">
        <rect x="18" y="6" width="14" height="12" fill="var(--red)"/>
        <rect x="68" y="6" width="14" height="12" fill="var(--red)"/>
        <rect x="6" y="16" width="88" height="10" fill="var(--red)"/>
        <rect x="8" y="30" width="84" height="52" fill="var(--red)"/>
        <path d="M18 44 H32 M25 37 V51" stroke="var(--white)" stroke-width="4"/>
        <path d="M68 44 H82" stroke="var(--white)" stroke-width="4"/>
      </svg>
    </div>
    <div class="menu-label">Options</div>
    <svg class="menu-rule" width="212" height="16" viewBox="0 0 212 16" aria-hidden="true">
      <rect x="0" y="10" width="212" height="4" fill="var(--black)"/>
      <path d="M190 14 L198 0 L212 14 Z" fill="var(--black)"/>
    </svg>
  </div>

</div>
</body>
</html>
```